Velk Partners Building Business Cards

We need a business card that reflects our business as "Solar Experts" in San Diego. Browse our website www.velkpartners.example our License needs to be displayed as "CSLB# 3867140" our phone number is (619) 555-0187

Save thousands on your electric bills and increase the value of your home while helping to protect the environment. Our solar installation experts will help you design the system that's right for you, using only the highest quality equipment that will look great and give you ideal performance. Our goal is to make you energy independent, and get your electric bill to 0.

Paul Osterby
(619) 555-0187
paul@velkpartners.example

Target Market(s)

Home owners in san diego looking for solar

Industry/Entity Type

Solar Energy

Contact Information for Business Card

Paul Osterby
(619) 555-0187
paul@velkpartners.example

Font styles to use
Other font styles liked:
• Use our logo font

Requirements
Must have
• License needs to be displayed as "CSLB# 3867140" our phone number is (619) 555-0187
Nice to have
• Real images of rooftop home solar in san diego
Should not have
• our business address

```html
<!DOCTYPE html>
<html lang="en">
<head>
<meta charset="utf-8">
<title>Velk Partners Building – Business Card</title>
<link href="https://fonts.googleapis.com/css2?family=Open+Sans:ital,wght@0,400;0,600;0,700;1,400&display=swap" rel="stylesheet">
<style>
  :root {
    --navy: #1b3f7a;
    --sun: #f6ae0f;
    --ink: #4d4d4d;
    --paper: #ffffff;
    --backdrop: #4a4a4a;
    --rule: #c9c9c9;
  }
  * { box-sizing: border-box; margin: 0; padding: 0; }
  html, body {
    width: 1105px;
    height: 1200px;
    overflow: hidden;
    background: var(--backdrop);
    font-family: "Open Sans", Arial, sans-serif;
  }
  .card {
    position: absolute;
    left: 193px;
    width: 719px;
    height: 410px;
    border-radius: 17px;
    overflow: hidden;
  }
  .card--front { top: 167px; background: var(--paper); }
  .card--back { top: 623px; background: var(--navy); }

  .brand-name {
    position: absolute;
    left: 52px;
    top: 151px;
    width: 300px;
    font-weight: 700;
    font-size: 31px;
    line-height: 1.1;
    color: var(--navy);
  }
  .divider {
    position: absolute;
    left: 384px;
    top: 93px;
    width: 1px;
    height: 175px;
    background: var(--rule);
  }
  .contact {
    position: absolute;
    left: 418px;
    top: 97px;
    color: var(--ink);
  }
  .contact__name {
    font-size: 25px;
    font-weight: 600;
    color: var(--navy);
    line-height: 1.2;
  }
  .contact__role {
    font-size: 20px;
    color: var(--sun);
    line-height: 1.2;
  }
  .contact__license {
    margin-top: 14px;
    font-size: 18px;
  }
  .contact__reach { margin-top: 12px; }
  .contact__line {
    display: flex;
    align-items: center;
    gap: 9px;
    font-size: 18px;
    line-height: 1.55;
  }
  .contact__line svg { width: 16px; height: 16px; fill: var(--navy); flex: none; }

  .front-band {
    position: absolute;
    left: 0;
    bottom: 0;
    width: 100%;
    height: 72px;
    background: var(--navy);
  }
  .front-web {
    position: absolute;
    right: 86px;
    top: 374px;
    font-size: 19px;
    color: var(--paper);
  }

  .back-mark {
    position: absolute;
    left: 0; right: 0;
    top: 168px;
    display: flex;
    align-items: center;
    justify-content: center;
    gap: 18px;
  }
  .back-mark__dot {
    width: 46px;
    height: 46px;
    border-radius: 50%;
    background: var(--sun);
  }
  .back-mark__name {
    font-weight: 700;
    font-size: 38px;
    color: var(--paper);
  }
  .back-web {
    position: absolute;
    left: 0; right: 0;
    top: 338px;
    text-align: center;
    font-style: italic;
    font-size: 19px;
    letter-spacing: 4px;
    color: var(--paper);
  }
</style>
</head>
<body>
  <section class="card card--front">
    <div class="brand-name">Velk Partners Building</div>
    <div class="divider"></div>
    <div class="contact">
      <p class="contact__name">Paul Osterby</p>
      <p class="contact__role">CEO/Founder</p>
      <p class="contact__license">CSLB# 3867140</p>
      <div class="contact__reach">
        <p class="contact__line">
          <svg viewBox="0 0 24 24" aria-hidden="true"><path d="M6.6 10.8a15.1 15.1 0 0 0 6.6 6.6l2.2-2.2a1 1 0 0 1 1-.25 11.4 11.4 0 0 0 3.6.57 1 1 0 0 1 1 1V20a1 1 0 0 1-1 1A17 17 0 0 1 3 4a1 1 0 0 1 1-1h3.5a1 1 0 0 1 1 1c0 1.25.2 2.46.57 3.6a1 1 0 0 1-.25 1z"/></svg>
          (619) 555-0187
        </p>
        <p class="contact__line">
          <svg viewBox="0 0 24 24" aria-hidden="true"><path d="M2 5h20v14H2z"/><path d="M3 6l9 7 9-7" fill="none" stroke="#fff" stroke-width="1.6"/></svg>
          paul@velkpartners.example
        </p>
      </div>
    </div>
    <div class="front-band" role="img" aria-label="Decorative wave band in navy and gold"></div>
    <p class="front-web">www.velkpartners.example</p>
  </section>

  <section class="card card--back">
    <div class="back-mark">
      <span class="back-mark__dot"></span>
      <span class="back-mark__name">Velk Partners Building</span>
    </div>
    <p class="back-web">www.velkpartners.example</p>
  </section>
</body>
</html>
```